Harbor Loom Floors Letterhead

Letterhead used for business reasons. It must be editable and easy to use.

Address is 2715 W. Pelican Lane Englewood FL 34187 - 941.382.6519

```html
<!DOCTYPE html>
<html lang="en">
<head>
<meta charset="utf-8">
<title>Harbor Loom Floors Letterhead</title>
<link rel="stylesheet" href="https://fonts.googleapis.com/css2?family=Montserrat:wght@400;600;700&family=Lato:wght@400&family=Kaushan+Script&display=swap">
<style>
  :root {
    --backdrop: #e9e9ea;
    --paper: #ffffff;
    --band: #181818;
    --accent: #e5952a;
    --ink: #1a1a1a;
    --band-text: #d9d9d9;
  }
  * { box-sizing: border-box; margin: 0; padding: 0; }
  html, body {
    width: 1200px; height: 874px; overflow: hidden;
    background: var(--backdrop);
  }
  .canvas {
    width: 1200px; height: 874px;
    display: flex; align-items: center; justify-content: center;
  }
  .letterhead {
    width: 590px; height: 834px;
    background: var(--paper);
    box-shadow: 0 6px 22px rgba(0,0,0,0.14);
    position: relative;
    font-family: "Montserrat", sans-serif;
    color: var(--ink);
  }
  .header-band {
    height: 150px; background: var(--band);
    position: relative;
  }
  .brand-name {
    position: absolute; left: 40px; bottom: 34px;
    font-family: "Montserrat", sans-serif;
    font-weight: 400; font-size: 26px; letter-spacing: 0.5px;
    color: var(--accent);
  }
  .contact-block {
    position: absolute; right: 40px; top: 38px;
    display: flex; gap: 14px; align-items: stretch;
  }
  .contact-rule { width: 1px; background: var(--accent); }
  .contact-lines {
    font-size: 9px; line-height: 1.55; letter-spacing: 0.3px;
    color: var(--band-text);
  }
  .contact-phone { display: flex; align-items: center; gap: 5px; }
  .contact-phone svg { width: 9px; height: 9px; }
  .letter-body {
    padding: 42px 70px 0 80px;
    font-size: 9.5px; line-height: 1.45;
  }
  .letter-date { margin-bottom: 14px; font-size: 10px; }
  .recipient { margin-bottom: 14px; }
  .recipient-address { margin-bottom: 22px; }
  .salutation { font-weight: 700; font-size: 12.5px; margin-bottom: 20px; }
  .letter-body p.paragraph { margin-bottom: 16px; }
  .closing { margin-top: 22px; }
  .signature {
    font-family: "Kaushan Script", cursive;
    font-size: 30px; margin-top: 28px;
  }
</style>
</head>
<body>
<div class="canvas">
  <article class="letterhead">
    <header class="header-band">
      <div class="brand-name">Harbor Loom Floors</div>
      <div class="contact-block">
        <span class="contact-rule"></span>
        <div class="contact-lines">
          <div>2715 W. Pelican Lane</div>
          <div>Englewood FL 34187</div>
          <div class="contact-phone">
            <svg viewBox="0 0 24 24" aria-hidden="true"><path fill="var(--accent)" d="M6.6 10.8a15.1 15.1 0 006.6 6.6l2.2-2.2a1 1 0 011-.25 11.4 11.4 0 003.6.57 1 1 0 011 1V20a1 1 0 01-1 1A17 17 0 013 4a1 1 0 011-1h3.5a1 1 0 011 1c0 1.25.2 2.45.57 3.57a1 1 0 01-.25 1z"/></svg>
            <span>941.382.6519</span>
          </div>
        </div>
      </div>
    </header>
    <section class="letter-body">
      <div class="letter-date">January-03-2020</div>
      <div class="recipient">Mr. Evan Hale<br>President</div>
      <div class="recipient-address">Brightway Holdings<br>123 Street Name, Suite# 10<br>City, State, 120023</div>
      <div class="salutation">Dear Mr, Evan</div>
      <p class="paragraph">Lorem ipsum dolor sit amet, consectetur adipiscing elit, sed do eiusmod tempor incididunt ut labore et dolore magna aliqua. Ut enim ad minim veniam, quis nostrud exercitation ullamco laboris nisi ut aliquip ex ea commodo consequat. Duis aute irure dolor in reprehenderit in voluptate velit esse cillum dolore eu fugiat nulla pariatur.</p>
      <p class="paragraph">Lorem ipsum dolor sit amet, consectetur adipiscing elit, sed do eiusmod tempor incididunt ut labore et dolore magna aliqua. Ut enim ad minim veniam, quis nostrud exercitation ullamco laboris nisi ut aliquip ex ea commodo consequat. Duis aute irure dolor in reprehenderit in voluptate velit esse cillum dolore eu fugiat nulla pariatur.</p>
      <p class="paragraph">Lorem ipsum dolor sit amet, consectetur adipiscing elit, sed do eiusmod tempor incididunt ut labore et dolore magna aliqua. Ut enim ad minim veniam, quis nostrud exercitation ullamco laboris nisi ut aliquip ex ea commodo consequat.</p>
      <p class="paragraph">Excepteur sint occaecat cupidatat non proident, sunt in culpa qui officia deserunt mollit anim id est laborum. re et dolore magnam aliquam quaerat voluptatem.</p>
      <div class="closing">Regards</div>
      <div class="signature">Nora Whitfield</div>
    </section>
  </article>
</div>
</body>
</html>
```